Real Estate Agent "Team" Ad that will go into the local newspaper

We need an ad design for the local newspaper. I've attached a copy of our last ad. We would like a little different design (use same content). The size is 4 inches tall x 6.5 inches wide. We would like to include our two photos. Keep it CLEAN and simple. We are a Mercer Island, Washington-based mother/daughter Ashford Realty real estate team focused exclusively on Mercer Island. The graphic design should reinforce the tone of warm/approachable, while clean and polished. The feel should be on-trend, current and clean/tight/contemporary. Should appeal to a high net worth consumer. The design should tell potential clients that Greta & Della are the premier, trusted team of advisors that informed buyers and sellers turn to for any residential real estate opportunities on Mercer Island.

Target Market(s)

Mercer Island Residents (past and potential customers). High-end, sophisticated Buyers.

Industry/Entity Type

Real Estate Agent

Font styles to use
Serif
Sans Serif

Colors
959595
5c5c5c
474747

Requirements
Must have
• Greta Harlow and Della Harlow Photos. Personal Logo. Ashford Realty Tull logo. Please keep colors simple (Black and White) with the exception of our photos and logos.
Nice to have
• Please keep Greta and Della Photos equal in size. This is a partnership.
Should not have
• No additional photos of houses or keys.

```html
<!DOCTYPE html>
<html lang="en">
<head>
<meta charset="utf-8">
<title>Greta Harlow &amp; Della Harlow Shea Real Estate – Newspaper Ad</title>
<link rel="stylesheet" href="https://fonts.googleapis.com/css2?family=Oswald:wght@300;400&family=Tinos:ital@0;1&display=swap">
<style>
  :root {
    --band-light: #959595;
    --band-dark: #474747;
    --ink: #474747;
    --ink-soft: #5c5c5c;
    --ink-muted: #7d7d7d;
    --paper: #ffffff;
    --accent: #c5cf2f;
    --photo-warm: #b9a89c;
    --photo-cool: #6e6560;
  }
  * { margin: 0; padding: 0; box-sizing: border-box; }
  html, body { width: 1200px; height: 738px; overflow: hidden; background: var(--paper); }
  .ad { position: relative; width: 1200px; height: 738px; background: var(--paper); overflow: hidden; }

  .top-band { position: absolute; left: 0; top: 0; width: 1200px; height: 172px; background: var(--band-light); }
  .brand-tab { position: absolute; left: 0; top: 15px; width: 456px; height: 142px; }
  .brand-mark { position: absolute; left: 72px; top: 58px; width: 54px; height: 54px; background: var(--accent); }
  .brand-name {
    position: absolute; left: 146px; top: 40px; width: 270px;
    font-family: "Oswald", sans-serif; font-weight: 300; color: var(--ink-muted);
    font-size: 26px; line-height: 31px; text-transform: uppercase; letter-spacing: 0.5px;
  }
  .brand-name .sub { display: block; font-size: 13px; line-height: 22px; letter-spacing: 9px; }

  .tagline {
    position: absolute; left: 505px; top: 28px; width: 600px; text-align: center;
    font-family: "Tinos", serif; font-style: italic; font-size: 49px; line-height: 54px; color: var(--ink);
  }

  .photo { position: absolute; top: 217px; width: 272px; height: 292px; }
  .photo--greta { left: 102px; background: linear-gradient(160deg, #d8d0c8, var(--photo-warm) 60%, #8e8e90); }
  .photo--della { left: 402px; background: linear-gradient(160deg, #8a817b, var(--photo-cool) 55%, #3e3a38); }
  .agent-phone {
    position: absolute; top: 522px; width: 300px; text-align: center;
    font-family: "Oswald", sans-serif; font-weight: 400; font-size: 29px; color: var(--ink-soft);
  }
  .agent-phone--greta { left: 88px; }
  .agent-phone--della { left: 388px; }

  .promise { position: absolute; left: 744px; top: 206px; font-family: "Tinos", serif; color: var(--ink); }
  .promise .lead { display: block; font-size: 45px; line-height: 44px; }
  .promise .place { display: block; font-size: 92px; line-height: 76px; margin-top: 4px; letter-spacing: 1px; }
  .promise .rest { display: block; font-size: 42px; line-height: 40px; margin-top: 4px; }

  .bottom-band { position: absolute; left: 0; top: 607px; width: 1200px; height: 131px; background: var(--band-dark); }
  .broker {
    position: absolute; left: 1030px; top: 619px; width: 158px; height: 107px;
    background: var(--paper); display: flex; align-items: center; justify-content: center; text-align: center;
    font-family: "Tinos", serif; font-size: 21px; line-height: 25px; color: var(--ink); letter-spacing: 1px;
  }
</style>
</head>
<body>
<main class="ad">
  <header class="top-band">
    <svg class="brand-tab" viewBox="0 0 456 142" aria-hidden="true">
      <polygon points="0,0 414,0 456,71 414,142 0,142" fill="#ffffff"/>
    </svg>
    <div class="brand-mark" aria-hidden="true"></div>
    <div class="brand-name">Greta Harlow &amp;<br>Della Harlow Shea<span class="sub">Real Estate</span></div>
    <p class="tagline">Opportunity is knocking –<br>Let us open the door</p>
  </header>

  <div class="photo photo--greta" role="img" aria-label="Portrait photo of Greta Harlow"></div>
  <div class="photo photo--della" role="img" aria-label="Portrait photo of Della Harlow"></div>
  <p class="agent-phone agent-phone--greta">GRETA: (206) 555-0147</p>
  <p class="agent-phone agent-phone--della">DELLA: (206) 555-0183</p>

  <p class="promise">
    <span class="lead">Your trusted</span>
    <span class="place">MERCER<br>ISLAND</span>
    <span class="rest">real estate team<br>for more than<br>40 years.</span>
  </p>

  <footer class="bottom-band"></footer>
  <div class="broker">ASHFORD<br>REALTY<br>TULL</div>
</main>
</body>
</html>
```